Marwick Partners Exit Plan business consultant web site

This website is for a consulting business that helps other businesses with exit plans. Essentially, assists them with the sale of their business. This website should be very professional, almost with a wall street look. I would like a very attractive image on the homepage. Perhaps something that denotes success. Perhaps a picture of palm trees and a beach? I will leave it to you for interpretation.

Across the screen I would like the words "Does your business have an exit plan?"

Below that it should read the following:
Let us help you with a completely impartial, no obligation assessment (button with link to the contact page)

Also, please use logo in a prominent place on the website so it's easily seen.

Target Market(s)

Males 40+

Coding

Coded - Design and coding required

Number of Pages Required

5+ page

Colors

Designer to choose colors to be used in the design.

Requirements
Must have
• The tabs for the homepage on the top should be:
• 1. About us
• 2. Services
• 3. Industries
• 4. Our success
• 5. Contact
Nice to have
• Clean, professional image.
• Please put FB, Twitter, Linked In - logos at bottom.
• Here are two examples of a website to give you an idea:
• https://notes.quelvarocapital.example/library/why-every-business-owner-should-have-an-exit-plan
Should not have
• nothing whimsical or cartoon like

```html
<!DOCTYPE html>
<html lang="en">
<head>
<meta charset="utf-8">
<title>Marwick Partners — Exit Planning Consultants</title>
<link rel="stylesheet" href="https://fonts.googleapis.com/css2?family=Libre+Baskerville:wght@400;700&family=Raleway:wght@400;500;600;700&display=swap">
<style>
:root{
  --blue:#1e86d2;
  --blue-dark:#176db0;
  --ink:#1a1a1a;
  --night:#151617;
  --text:#555a60;
  --muted:#8a8f95;
  --white:#ffffff;
  --line:#e6e8eb;
  --serif:'Libre Baskerville', Georgia, serif;
  --sans:'Raleway', Arial, sans-serif;
}
*{box-sizing:border-box;margin:0;padding:0}
html,body{width:1200px;height:4437px;overflow:hidden}
body{position:relative;font-family:var(--sans);color:var(--text);background:var(--white)}
a{color:inherit;text-decoration:none}
section,header,footer{position:absolute;left:0;width:1200px}

/* header */
.site-header{top:0;height:124px;background:var(--white)}
.brand{position:absolute;left:90px;top:20px;display:flex;align-items:center;gap:12px}
.brand-square{width:46px;height:46px;background:var(--ink)}
.brand-name{font-family:var(--serif);font-size:24px;color:var(--ink);letter-spacing:1px}
.topbar{position:absolute;right:90px;top:28px;display:flex;gap:40px;font-size:15px;color:var(--ink);font-weight:500}
.topbar span{display:flex;align-items:center;gap:10px}
.nav{position:absolute;right:90px;top:77px;display:flex;gap:38px;font-size:15.5px;color:var(--ink)}
.nav .active{color:var(--blue);border-bottom:1px solid var(--blue)}

/* hero */
.hero{top:124px;height:620px;background:linear-gradient(90deg,#f3f4f6 0%,#e8e4df 45%,#b9a597 75%,#5e4a3f 100%)}
.hero-photo{position:absolute;inset:0}
.hero-kicker{position:absolute;left:87px;top:134px;font-family:var(--serif);font-size:33px;color:var(--ink)}
.hero-title{position:absolute;left:88px;top:191px;font-family:var(--serif);font-weight:700;font-size:37px;line-height:46px;color:var(--blue);letter-spacing:.5px}
.btn{display:inline-flex;align-items:center;gap:10px;background:var(--blue);color:var(--white);font-family:var(--sans);font-weight:700;font-size:15px;padding:0 24px;height:50px}
.hero .btn{position:absolute;left:90px;top:313px;width:182px}
.mouse{position:absolute;left:92px;top:404px}

/* help band */
.help{top:744px;height:286px;background:var(--night)}
.help-icon-box{position:absolute;left:90px;top:0;width:340px;height:286px;background:var(--blue);display:flex;align-items:center;justify-content:center}
.help-title{position:absolute;left:543px;top:50px;font-family:var(--serif);font-weight:400;font-size:38px;line-height:64px;color:var(--white)}
.help-text{position:absolute;left:793px;top:62px;width:330px;font-size:19px;line-height:30px;color:var(--white)}
.help .btn{position:absolute;left:793px;top:164px;height:48px}

/* about */
.about{top:1030px;height:580px;background:linear-gradient(110deg,#f4f0f0 0%,#e9e1e3 30%,#d8c9cc 50%,#8d95a6 75%,#4c5c70 100%)}
.about-photo{position:absolute;inset:0}
.about h2{position:absolute;left:89px;top:115px;font-family:var(--serif);font-weight:400;font-size:43px;color:var(--ink)}
.about h2 em{font-style:normal;color:var(--blue)}
.about p{position:absolute;left:89px;top:174px;width:480px;font-size:16px;line-height:35px;color:var(--ink)}
.about .btn{position:absolute;left:90px;top:404px;width:182px}

/* industries */
.industries{top:1610px;height:563px;background:linear-gradient(180deg,#1b1c1e 0%,#25282b 100%)}
.industries h2{position:absolute;left:0;width:1200px;text-align:center;top:88px;font-family:var(--serif);font-weight:400;font-size:43px;color:var(--white)}
.industry{position:absolute;top:155px;width:331px;height:280px}
.industry-photo{position:absolute;inset:0}
.industry-label{position:absolute;left:20px;right:20px;top:186px;height:68px;background:var(--blue);color:var(--white);font-size:18px;line-height:23px;padding:12px 15px}
.industry-go{position:absolute;right:0;top:0;width:64px;height:68px;background:var(--ink);display:flex;align-items:center;justify-content:center}

/* services */
.services{top:2173px;height:1026px;background:var(--white)}
.services h2{position:absolute;left:0;width:1200px;text-align:center;top:116px;font-family:var(--serif);font-weight:400;font-size:43px;color:var(--ink)}
.services h2 em{font-style:normal;color:var(--blue)}
.service{position:absolute;width:326px;height:284px;background:var(--white);box-shadow:0 4px 14px rgba(0,0,0,.13);padding:0 26px}
.service-icon{position:absolute;left:26px;top:-38px;width:74px;height:74px;background:var(--blue);display:flex;align-items:center;justify-content:center}
.service h3{margin-top:66px;font-size:21px;font-weight:600;color:var(--ink);letter-spacing:.5px}
.service p{margin-top:18px;font-size:15.5px;line-height:29px;color:var(--muted)}
.service .more{display:block;margin-top:16px;font-size:13px;font-weight:700;color:var(--blue)}
.service.featured{background:var(--blue)}
.service.featured .service-icon{background:var(--white);border:1px solid var(--blue)}
.service.featured h3,.service.featured p,.service.featured .more{color:var(--white)}

/* success */
.success{top:3199px;height:288px;background:linear-gradient(90deg,#161718 0%,#1c1d1f 60%,#3a3431 100%)}
.success h2{position:absolute;left:90px;top:54px;font-family:var(--serif);font-weight:400;font-size:39px;line-height:51px;color:var(--white)}
.success p{position:absolute;left:340px;top:66px;width:390px;font-size:19px;line-height:30px;color:var(--white)}
.success .btn{position:absolute;left:341px;top:184px;height:48px}
.success-icon-box{position:absolute;left:770px;top:0;width:339px;height:288px;background:var(--blue);display:flex;align-items:center;justify-content:center}
.workshop{top:3487px;height:413px;background:linear-gradient(160deg,#d9d9d7 0%,#ecebe8 45%,#c7c3bd 100%)}

/* footer */
.site-footer{top:3900px;height:537px;background:var(--night);color:var(--white)}
.footer-arrow{position:absolute;left:589px;top:0}
.footer-brand{position:absolute;left:90px;top:104px;width:190px;display:flex;flex-direction:column;align-items:center;gap:8px}
.footer-brand .brand-square{width:34px;height:40px;background:var(--white)}
.footer-brand .brand-name{color:var(--white);font-size:14px;letter-spacing:.5px}
.footer-col h4{font-family:var(--sans);font-weight:500;font-size:27px;color:var(--white)}
.newsletter{position:absolute;left:312px;top:105px;width:310px}
.newsletter p{margin-top:28px;font-size:13px;line-height:22px}
.newsletter .field{margin-top:20px;width:306px;height:42px;border-radius:21px;background:var(--white);color:#666;font-size:11px;padding:14px 18px}
.newsletter .signup{margin-top:16px;width:128px;height:38px;border-radius:19px;background:var(--blue);font-weight:600;font-size:16px;display:flex;align-items:center;justify-content:center}
.links{position:absolute;left:686px;top:105px}
.links ul{list-style:none;margin-top:26px;font-size:14px;line-height:29.5px}
.contact{position:absolute;left:886px;top:105px;width:240px}
.contact-row{display:flex;gap:18px;margin-top:22px;font-size:13px;line-height:20px}
.contact-row:first-of-type{margin-top:28px}
.contact-pin{flex:0 0 30px;height:30px;background:var(--blue);display:flex;align-items:center;justify-content:center}
.copyright{position:absolute;left:0;width:1200px;text-align:center;top:413px;font-size:13px}
.socials{position:absolute;left:520px;top:450px;display:flex;gap:18px}
.socials span{width:42px;height:42px;border:2px solid var(--white);border-radius:50%;display:flex;align-items:center;justify-content:center}
.socials span i{width:8px;height:8px;background:var(--white);border-radius:50%}
</style>
</head>
<body>

<header class="site-header">
  <div class="brand"><span class="brand-square"></span><span class="brand-name">MARWICK PARTNERS</span></div>
  <div class="topbar">
    <span><svg width="18" height="18" viewBox="0 0 18 18"><rect width="18" height="18" rx="3" fill="#1e86d2"/><path d="M6 4l2 2-1 1.5c.7 1.5 1.8 2.6 3.3 3.3L12 9.8l2 2-1 2c-4.5 0-8.8-4.3-8.8-8.8z" fill="#fff"/></svg>+1 555 0142 7730</span>
    <span><svg width="18" height="18" viewBox="0 0 18 18"><rect width="18" height="18" rx="3" fill="#1e86d2"/><rect x="4" y="5.5" width="10" height="7" fill="#fff"/><path d="M4 5.5l5 4 5-4" stroke="#1e86d2" fill="none"/></svg>info@marwickpartners.example</span>
  </div>
  <nav class="nav">
    <a class="active">Home</a><a>About Us</a><a>Services</a><a>Industries</a><a>Our Success</a><a>Contact</a>
  </nav>
</header>

<section class="hero">
  <div class="hero-photo" role="img" aria-label="Photo of a consultant in a navy suit talking across a desk with a client in a bright office"></div>
  <div class="hero-kicker">MARWICK PARTNERS</div>
  <h1 class="hero-title">DOES YOUR BUSINESS HAVE<br>AN EXIT PLAN?</h1>
  <a class="btn">LEARN MORE <svg width="14" height="14" viewBox="0 0 14 14"><circle cx="7" cy="7" r="7" fill="#fff"/><path d="M5.5 4l3 3-3 3" stroke="#1e86d2" stroke-width="2" fill="none"/></svg></a>
  <svg class="mouse" width="28" height="46" viewBox="0 0 28 46"><rect x="2" y="2" width="24" height="42" rx="12" fill="none" stroke="#1a1a1a" stroke-width="2.5"/><line x1="14" y1="9" x2="14" y2="17" stroke="#1a1a1a" stroke-width="2.5"/></svg>
</section>

<section class="help">
  <div class="help-icon-box">
    <svg width="100" height="90" viewBox="0 0 100 90" fill="none" stroke="#fff" stroke-width="3" stroke-linecap="round">
      <circle cx="48" cy="36" r="15"/>
      <path d="M28 38c0-14 9-24 20-24s20 10 20 24"/>
      <path d="M26 80c2-14 11-22 22-22s20 8 22 22"/>
      <path d="M82 20c8 8 8 22 0 30"/><path d="M78 46l5 4 3-6"/>
      <path d="M14 52l8-8 6 6-4 6c3 5 6 8 10 10"/>
    </svg>
  </div>
  <h2 class="help-title">LET US<br>HELP<br>YOU</h2>
  <p class="help-text">Let us help you with a completely impartial, no obligation assessment</p>
  <a class="btn">CONTACT US <svg width="14" height="14" viewBox="0 0 14 14"><circle cx="7" cy="7" r="7" fill="#fff"/><path d="M5.5 4l3 3-3 3" stroke="#1e86d2" stroke-width="2" fill="none"/></svg></a>
</section>

<section class="about">
  <div class="about-photo" role="img" aria-label="Double-exposure image of business people silhouettes over a city skyline at sunrise"></div>
  <h2>ABOUT <em>US</em></h2>
  <p>Lorem ipsum dolor sit amet, consectetur adipiscing elit, sed do eiusmod tempor incididunt ut labore et dolore magna aliqua. Ut enim ad minim veniam, quis nostrud exercitation ullamco laboris nisi ut aliquip ex ea commodo consequat. Duis aute irure dolor in reprehenderit in voluptate velit esse cillum dolore eu fugiat nulla pariatur.</p>
  <a class="btn">LEARN MORE <svg width="14" height="14" viewBox="0 0 14 14"><circle cx="7" cy="7" r="7" fill="#fff"/><path d="M5.5 4l3 3-3 3" stroke="#1e86d2" stroke-width="2" fill="none"/></svg></a>
</section>

<section class="industries">
  <h2>INDUSTRIES</h2>
  <div class="industry" style="left:90px">
    <div class="industry-photo" role="img" aria-label="Team joining hands over a desk of charts and laptops" style="background:linear-gradient(135deg,#5b6d78,#8fa0a8 50%,#6c7a80)"></div>
    <div class="industry-label">Lorem ipsum<br>dolor<span class="industry-go"><svg width="14" height="20" viewBox="0 0 14 20"><path d="M3 3l7 7-7 7" stroke="#fff" stroke-width="2.5" fill="none"/></svg></span></div>
  </div>
  <div class="industry" style="left:434px">
    <div class="industry-photo" role="img" aria-label="Businessman signing documents at a white desk" style="background:linear-gradient(135deg,#e9ecee,#c9ced2 55%,#7d858b)"></div>
    <div class="industry-label">Lorem ipsum<br>dolor<span class="industry-go"><svg width="14" height="20" viewBox="0 0 14 20"><path d="M3 3l7 7-7 7" stroke="#fff" stroke-width="2.5" fill="none"/></svg></span></div>
  </div>
  <div class="industry" style="left:778px">
    <div class="industry-photo" role="img" aria-label="Office towers seen from below against a blue sky" style="background:linear-gradient(160deg,#3f78b8,#8db3d8 45%,#3a3f48)"></div>
    <div class="industry-label">Lorem ipsum<br>dolor<span class="industry-go"><svg width="14" height="20" viewBox="0 0 14 20"><path d="M3 3l7 7-7 7" stroke="#fff" stroke-width="2.5" fill="none"/></svg></span></div>
  </div>
</section>

<section class="services">
  <h2>OUR <em>SERVICES</em></h2>

  <article class="service" style="left:90px;top:246px">
    <div class="service-icon"><svg width="36" height="30" viewBox="0 0 36 30" fill="#fff"><circle cx="18" cy="8" r="6"/><circle cx="7" cy="10" r="4"/><circle cx="29" cy="10" r="4"/><path d="M8 28c0-7 4-11 10-11s10 4 10 11z"/><path d="M0 26c0-5 3-8 7-8 1 0 2 0 3 1-2 2-3 5-3 7z"/><path d="M36 26c0-5-3-8-7-8-1 0-2 0-3 1 2 2 3 5 3 7z"/></svg></div>
    <h3>ORGANISATION</h3>
    <p>Sed ut perspiciatis unde omnis iste natus error sit voluptatem ccusantium doloremque laudantium, totam rem aperiam.</p>
    <a class="more">READ MORE »</a>
  </article>
  <article class="service" style="left:437px;top:246px">
    <div class="service-icon"><svg width="34" height="28" viewBox="0 0 34 28" fill="none" stroke="#fff" stroke-width="3"><path d="M2 2v24h30"/><path d="M7 20l7-8 5 5 10-11"/></svg></div>
    <h3>STRATEGY</h3>
    <p>Sed ut perspiciatis unde omnis iste natus error sit voluptatem ccusantium doloremque laudantium, totam rem aperiam.</p>
    <a class="more">READ MORE »</a>
  </article>
  <article class="service" style="left:785px;top:246px">
    <div class="service-icon"><svg width="32" height="32" viewBox="0 0 32 32" fill="none" stroke="#fff" stroke-width="4"><path d="M5 14a11 11 0 0 1 20-5"/><path d="M27 18a11 11 0 0 1-20 5"/><path d="M26 3v7h-7" stroke-width="3"/><path d="M6 29v-7h7" stroke-width="3"/></svg></div>
    <h3>PROCESS</h3>
    <p>Sed ut perspiciatis unde omnis iste natus error sit voluptatem ccusantium doloremque laudantium, totam rem aperiam.</p>
    <a class="more">READ MORE »</a>
  </article>

  <article class="service" style="left:90px;top:616px">
    <div class="service-icon"><svg width="32" height="32" viewBox="0 0 32 32"><circle cx="16" cy="16" r="10" fill="none" stroke="#fff" stroke-width="7" stroke-dasharray="5 3"/><circle cx="16" cy="16" r="8" fill="#fff"/><circle cx="16" cy="16" r="4" fill="#1e86d2"/></svg></div>
    <h3>EFFICIENT</h3>
    <p>Sed ut perspiciatis unde omnis iste natus error sit voluptatem ccusantium doloremque laudantium, totam rem aperiam.</p>
    <a class="more">READ MORE »</a>
  </article>
  <article class="service featured" style="left:437px;top:616px">
    <div class="service-icon"><svg width="34" height="32" viewBox="0 0 34 32" fill="#1e86d2"><path d="M33 1L1 14l9 4 17-12-13 15 11 9z"/><path d="M10 20v10l5-6z"/></svg></div>
    <h3>IMPROVEMENT</h3>
    <p>Sed ut perspiciatis unde omnis iste natus error sit voluptatem ccusantium doloremque laudantium, totam rem aperiam.</p>
    <a class="more">READ MORE »</a>
  </article>
  <article class="service" style="left:785px;top:616px">
    <div class="service-icon"><svg width="24" height="34" viewBox="0 0 24 34" fill="none" stroke="#fff" stroke-width="3"><path d="M7 24c0-5-5-7-5-13a10 10 0 0 1 20 0c0 6-5 8-5 13z"/><path d="M8 29h8M9 33h6"/></svg></div>
    <h3>EXPERTISE</h3>
    <p>Sed ut perspiciatis unde omnis iste natus error sit voluptatem ccusantium doloremque laudantium, totam rem aperiam.</p>
    <a class="more">READ MORE »</a>
  </article>
</section>

<section class="success">
  <h2>OUR<br>SUCCESS</h2>
  <p>Lorem ipsum dolor sit amet, consectetur adipiscing elit, sed do eiusmod tempor incididunt ut labore et dolore</p>
  <a class="btn">CONTACT US <svg width="14" height="14" viewBox="0 0 14 14"><circle cx="7" cy="7" r="7" fill="#fff"/><path d="M5.5 4l3 3-3 3" stroke="#1e86d2" stroke-width="2" fill="none"/></svg></a>
  <div class="success-icon-box">
    <svg width="96" height="96" viewBox="0 0 96 96" fill="none" stroke="#fff" stroke-width="3" stroke-linecap="round">
      <path d="M58 8v40"/><path d="M58 10h26l-6 7 6 7H58"/>
      <circle cx="30" cy="24" r="7"/><path d="M22 46l8-14 10 6 10-10"/><path d="M30 46v14"/>
      <path d="M8 60c8 0 10 10 10 24M88 60c-8 0-10 10-10 24"/>
      <path d="M30 60c10 0 14 8 14 24M66 60c-10 0-14 8-14 24"/>
    </svg>
  </div>
</section>

<section class="workshop" role="img" aria-label="Team leaning over a table sketching a plan with sticky notes and coffee cups"></section>

<footer class="site-footer">
  <svg class="footer-arrow" width="22" height="44" viewBox="0 0 22 44"><path d="M6 8l5-5 5 5" stroke="#1a1a1a" stroke-width="2" fill="none"/></svg>
  <div class="footer-brand"><span class="brand-square"></span><span class="brand-name">MARWICK PARTNERS</span></div>

  <div class="footer-col newsletter">
    <h4>Sign up for newsletter</h4>
    <p>Excepteur sint occaecat cupidatat non proident, sunt in culpa qui officia deserunt</p>
    <div class="field">Enter email</div>
    <div class="signup">SIGN UP</div>
  </div>

  <div class="footer-col links">
    <h4>Quick Links</h4>
    <ul><li>Home</li><li>About Us</li><li>Services</li><li>Industries</li><li>Our Success</li><li>Contact</li></ul>
  </div>

  <div class="footer-col contact">
    <h4>Contact Us</h4>
    <div class="contact-row"><span class="contact-pin"><svg width="14" height="18" viewBox="0 0 14 18"><path d="M7 17S1 10 1 7a6 6 0 0 1 12 0c0 3-6 10-6 10z" fill="#fff"/><circle cx="7" cy="7" r="2.2" fill="#1e86d2"/></svg></span><span>Marwick Advisory<br>210 Harbor Avenue, 12th floor<br>Easton, ST 00412</span></div>
    <div class="contact-row"><span class="contact-pin"><svg width="16" height="16" viewBox="0 0 16 16"><path d="M4 1l3 3-1.5 2c.8 1.8 2.2 3.2 4 4L11.5 8.5l3 3-1.5 3C7 14.5 1.5 9 1.5 2.5z" fill="none" stroke="#fff" stroke-width="1.4"/></svg></span><span>Call us today:<br>(555) 014-2290</span></div>
    <div class="contact-row"><span class="contact-pin"><svg width="16" height="12" viewBox="0 0 16 12" fill="none" stroke="#fff" stroke-width="1.4"><rect x="1" y="1" width="14" height="10"/><path d="M1 1l7 6 7-6"/></svg></span><span>Email :<br>mail@marwick.example</span></div>
  </div>

  <div class="copyright">© Copyright 2020 Marwick Partners. All Rights Reserved.</div>
  <div class="socials">
    <span role="img" aria-label="Social profile link"><i></i></span>
    <span role="img" aria-label="Social profile link"><i></i></span>
    <span role="img" aria-label="Social profile link"><i></i></span>
  </div>
</footer>

</body>
</html>
```